Need Flyer for Our Real estate Agency

Need to run General Campaign for our agency with Start of New Year as our theme ..Must have an agent's picture on the DL..
Address:
27 / 486Brindle rd, Marsden VIC 3047
Ph:03 9412 7306
email:info@kovalinrealestate.com.au
www.kovalinrealestate.com.au
Something like as attached picture..
Target Market(s)
Home Buyers
Industry/Entity Type
Real Estate Agent
Requirements
Must have
- Our Logo Colours

```html
<!DOCTYPE html>
<html lang="en">
<head>
<meta charset="utf-8">
<title>Kovalin – New Year DL Flyer</title>
<link href="https://fonts.googleapis.com/css2?family=Lato:wght@300;400;700;900&display=swap" rel="stylesheet">
<style>
  :root{
    --page:#e9e9eb;
    --navy-deep:#0b1f4d;
    --navy:#1a3778;
    --red:#7a1320;
    --grey-swoosh:#c9c9cc;
    --white:#ffffff;
    --pill-text:#7a1320;
  }
  *{margin:0;padding:0;box-sizing:border-box}
  html,body{width:1200px;height:1199px;overflow:hidden;background:var(--page);font-family:"Lato",sans-serif}
  .flyer{position:absolute;left:117px;width:966px;height:460px;overflow:hidden;box-shadow:0 6px 18px rgba(0,0,0,.25)}
  .flyer--front{top:113px}
  .flyer--back{top:644px}
  .flyer__bg{position:absolute;inset:0}
  .brand{position:absolute;left:0;width:100%;text-align:center;color:var(--white)}
  .brand__name{position:absolute;left:470px;width:464px;top:118px;text-align:center;color:var(--white);font-weight:400;font-size:50px;letter-spacing:6px}
  .headline{position:absolute;left:470px;width:464px;top:212px;text-align:center;color:var(--white);font-weight:300;font-size:30px;line-height:45px}
  .subline{position:absolute;left:440px;width:524px;top:323px;text-align:center;color:var(--white);font-weight:400;font-size:15.5px;letter-spacing:.2px}
  .subline strong{font-weight:900}
  .cta{position:absolute;left:521px;top:372px;width:362px;height:47px;border-radius:24px;background:var(--white);box-shadow:0 3px 8px rgba(0,0,0,.3);display:flex;align-items:center;justify-content:center;gap:8px;color:var(--pill-text);font-weight:900;font-size:20px}
  .cta svg{width:20px;height:20px}
  .cta__note{position:absolute;left:470px;width:464px;top:428px;text-align:center;color:var(--white);font-size:16px;font-weight:400}
  .contact{position:absolute;left:586px;list-style:none;color:var(--white);font-size:17px;font-weight:400}
  .contact li{display:flex;align-items:center;gap:12px;height:41px}
  .contact svg{width:18px;height:18px}
  .address{position:absolute;left:470px;width:464px;top:414px;text-align:center;color:var(--white);font-size:17px;letter-spacing:.3px}
</style>
</head>
<body>

<!-- Front: agent campaign side -->
<section class="flyer flyer--front">
  <svg class="flyer__bg" viewBox="0 0 966 460" width="966" height="460">
    <defs>
      <linearGradient id="navyFront" x1="0" y1="0" x2="1" y2="0">
        <stop offset="0" stop-color="#0b1f4d"/>
        <stop offset="1" stop-color="#1a3778"/>
      </linearGradient>
      <linearGradient id="agentPhoto" x1="0" y1="0" x2="0" y2="1">
        <stop offset="0" stop-color="#b9c7dc"/>
        <stop offset=".55" stop-color="#9aa3b0"/>
        <stop offset="1" stop-color="#2d3f70"/>
      </linearGradient>
    </defs>
    <rect width="966" height="460" fill="url(#navyFront)"/>
    <rect y="392" width="966" height="68" fill="var(--red)"/>
    <rect y="389" width="966" height="3" fill="var(--white)"/>
    <path d="M0 0 L395 0 Q500 230 385 460 L0 460 Z" fill="var(--grey-swoosh)"/>
    <path d="M0 0 L300 0 Q470 230 372 460 L0 460 Z" fill="var(--white)"/>
    <path role="img" aria-label="Photo of the agent in a suit standing in front of a large family home at dusk" d="M0 0 L275 0 Q450 230 355 460 L0 460 Z" fill="url(#agentPhoto)"/>
  </svg>
  <div class="brand__name">KOVALIN</div>
  <p class="headline">Curios to know what your<br>home is worth?</p>
  <p class="subline">START OF NEW YEAR WITH <strong>ROHAN MEHTA</strong> AND FIND OUT!</p>
  <div class="cta">CALL ME NOW!
    <svg viewBox="0 0 24 24" aria-hidden="true"><circle cx="12" cy="12" r="10.5" fill="none" stroke="currentColor" stroke-width="2"/><path d="M8.3 6.8c.4-.4 1-.4 1.3 0l1.2 1.6c.3.4.2.9-.1 1.2l-.7.7c.6 1.3 1.6 2.3 2.9 2.9l.7-.7c.3-.3.8-.4 1.2-.1l1.6 1.2c.4.3.4.9 0 1.3l-.8.8c-.6.6-1.6.8-2.4.4-2.4-1.1-4.3-3-5.4-5.4-.4-.8-.2-1.8.4-2.4z" fill="currentColor"/></svg>
    03 9412 7306</div>
  <p class="cta__note">For Free property Appraisal</p>
</section>

<!-- Back: contact side -->
<section class="flyer flyer--back">
  <svg class="flyer__bg" viewBox="0 0 966 460" width="966" height="460">
    <defs>
      <linearGradient id="navyBack" x1="0" y1="0" x2="1" y2="0">
        <stop offset="0" stop-color="#0b1f4d"/>
        <stop offset="1" stop-color="#1a3778"/>
      </linearGradient>
      <linearGradient id="housePhoto" x1="0" y1="0" x2="1" y2="1">
        <stop offset="0" stop-color="#1d2d4f"/>
        <stop offset=".5" stop-color="#c9a08a"/>
        <stop offset="1" stop-color="#2a3656"/>
      </linearGradient>
    </defs>
    <rect width="966" height="460" fill="url(#navyBack)"/>
    <rect y="392" width="966" height="68" fill="var(--red)"/>
    <rect y="389" width="966" height="3" fill="var(--white)"/>
    <path d="M0 0 L395 0 Q500 230 385 460 L0 460 Z" fill="var(--grey-swoosh)"/>
    <path d="M0 0 L300 0 Q470 230 372 460 L0 460 Z" fill="var(--white)"/>
    <path role="img" aria-label="Photo of two hands sheltering a small red model house" d="M0 0 L275 0 Q450 230 355 460 L0 460 Z" fill="url(#housePhoto)"/>
  </svg>
  <div class="brand__name">KOVALIN</div>
  <ul class="contact" style="top:222px">
    <li><svg viewBox="0 0 24 24" aria-hidden="true"><circle cx="12" cy="12" r="10.5" fill="none" stroke="#fff" stroke-width="2"/><path d="M8.3 6.8c.4-.4 1-.4 1.3 0l1.2 1.6c.3.4.2.9-.1 1.2l-.7.7c.6 1.3 1.6 2.3 2.9 2.9l.7-.7c.3-.3.8-.4 1.2-.1l1.6 1.2c.4.3.4.9 0 1.3l-.8.8c-.6.6-1.6.8-2.4.4-2.4-1.1-4.3-3-5.4-5.4-.4-.8-.2-1.8.4-2.4z" fill="#fff"/></svg>03 9412 7306</li>
    <li><svg viewBox="0 0 24 24" aria-hidden="true"><circle cx="12" cy="12" r="10.5" fill="none" stroke="#fff" stroke-width="2"/><rect x="6.5" y="8" width="11" height="8" rx="1" fill="none" stroke="#fff" stroke-width="1.6"/><path d="M6.8 8.5 12 12.5l5.2-4" fill="none" stroke="#fff" stroke-width="1.6"/></svg>info@kovalinrealestate.com.au</li>
    <li><svg viewBox="0 0 24 24" aria-hidden="true"><circle cx="12" cy="12" r="10.5" fill="none" stroke="#fff" stroke-width="2"/><circle cx="12" cy="12" r="6" fill="none" stroke="#fff" stroke-width="1.4"/><path d="M6 12h12M12 6c-2.5 3.5-2.5 8.5 0 12M12 6c2.5 3.5 2.5 8.5 0 12" fill="none" stroke="#fff" stroke-width="1.2"/></svg>www.kovalinrealestate.com.au</li>
  </ul>
  <p class="address">27 / 486 Brindle Rd, Marsden VIC 3047</p>
</section>

</body>
</html>
```